TREVAL BUILDWORKS, LLC Webpage portfolio

I want to create a Website that allows my potential clients to browse my Skilled work via before and after photos. I want the website to enhance the work that I provide and potentially drive new business, or at least solidify my work.
I also do 3D CAD and Modeling of New Spaces and it would be nice to show some of that work from pencil design to 3D modeling, which I feel may help give me more clients.

The website needs to show a solid carpenter/company with the skills to get any project completed.

Types of Jobs - Custom Carpentry & Finishes, Kitchens, Baths, Basements, Decks, Porches, Whole House Renovation - Skilled Craftsmanship (Hardwood Flooring, Floor and Wall Tile) and much more...

Target Market(s)

Residential Home Renovation, Kitchen and Bath Renovation, Home Improvement

Industry/Entity Type

Residential Construction

Number of Pages Required

5+ page

Font styles to use
Sans Serif
Script

Requirements
Must have
• Similar to Plinvo.com, except for Treval Buildworks.
• Must be inviting.
• My Services Offered
• A way to reach me or contact me for estimates with some sort of Screening Questionare.
Nice to have
• Inviting Colors
Should not have
• Not sure at this time

```html
<!DOCTYPE html>
<html lang="en">
<head>
<meta charset="utf-8">
<title>Treval Buildworks — Portfolio</title>
<link rel="stylesheet" href="https://fonts.googleapis.com/css2?family=Montserrat:wght@300;400;500&family=Questrial&display=swap">
<style>
  :root {
    --wood: #d9a96c;
    --wood-light: #e4b87e;
    --wood-dark: #c89356;
    --grain-dark: rgba(150, 95, 40, 0.22);
    --grain-soft: rgba(150, 95, 40, 0.12);
    --grain-light: rgba(255, 235, 200, 0.22);
    --ink: #3b2a1c;
    --ink-soft: #4a3726;
    --shadow: rgba(60, 35, 10, 0.45);
  }
  * { margin: 0; padding: 0; box-sizing: border-box; }
  html, body { width: 738px; height: 1200px; overflow: hidden; }

  /* wood grain surface shared by page, planks and frames */
  .wood {
    background-color: var(--wood);
    background-image:
      repeating-linear-gradient(90deg, transparent 0 7px, var(--grain-dark) 7px 8px, transparent 8px 19px, var(--grain-soft) 19px 21px, transparent 21px 31px),
      repeating-linear-gradient(90deg, transparent 0 3px, var(--grain-light) 3px 5px, transparent 5px 13px, var(--grain-soft) 13px 14px, transparent 14px 23px),
      repeating-linear-gradient(90deg, transparent 0 41px, var(--grain-dark) 41px 43px, transparent 43px 67px, var(--grain-light) 67px 71px, transparent 71px 97px),
      linear-gradient(90deg, var(--wood-dark) 0%, var(--wood-light) 20%, var(--wood) 40%, var(--wood-light) 55%, var(--wood) 75%, var(--wood-light) 90%, var(--wood-dark) 100%);
  }
  body {
    position: relative;
    font-family: "Questrial", sans-serif;
    color: var(--ink);
  }
  .abs { position: absolute; }

  /* header */
  .brand { left: 32px; top: 34px; display: flex; align-items: center; gap: 6px;
    font-family: "Montserrat", sans-serif; font-weight: 500; font-size: 11px; color: var(--ink-soft); }
  .brand-mark { width: 10px; height: 10px; background: var(--ink-soft); }
  .social { display: flex; gap: 9px; }
  .social span { width: 9px; height: 9px; border-radius: 2px; border: 1.5px solid var(--ink-soft); display: block; }
  .social-top { left: 509px; top: 12px; }
  .phone { right: 31px; top: 12px; font-size: 7px; letter-spacing: .3px; }
  .main-nav { right: 31px; top: 61px; display: flex; gap: 12px;
    font-family: "Questrial", sans-serif; font-size: 8.6px; letter-spacing: .2px; }

  /* section headings & planks */
  .section-title { left: 31px; font-family: "Montserrat", sans-serif; font-weight: 300;
    font-size: 20px; line-height: 26.5px; letter-spacing: .2px; color: var(--ink-soft); text-transform: uppercase; }
  .plank { left: 0; width: 369px; height: 20px;
    box-shadow: 0 1px 0 rgba(255,230,190,.5) inset, 0 5px 7px var(--shadow); }

  .side-copy { left: 31px; width: 104px; font-size: 6.4px; line-height: 8.8px; text-transform: uppercase; }
  .side-copy p { margin-bottom: 9px; }
  .side-copy .lead { font-size: 9.6px; line-height: 13px; margin-bottom: 0; margin-top: 12px; }

  /* framed showcases */
  .frame { left: 185px; width: 521px;
    box-shadow: 0 0 0 1px rgba(255,230,190,.35) inset, 0 7px 12px var(--shadow); }
  .frame-media { position: absolute; left: 30px; top: 30px; width: 462px; height: 184px; }
  .media-cad { display: flex; }
  .media-cad div { flex: 1; }

  .arrows { left: 31px; top: 594px; }
  .thumb { left: 30px; top: 615px; width: 155px; height: 154px;
    background: linear-gradient(160deg, #6b4a30, #3a2a22 60%, #2a231f); }
  .social-mid { left: 31px; top: 781px; }

  /* testimonials */
  .cards { left: 185px; top: 922px; display: flex; gap: 25px; }
  .card { width: 80px; font-size: 6.4px; line-height: 8.8px; }
  .card-photo { width: 80px; height: 80px; background: linear-gradient(#4a4a58, #2d2f3c); margin-bottom: 22px; }
  .card-name { margin-top: 21px; font-size: 9.2px; line-height: 11.5px; letter-spacing: .3px; }
  .card-role { font-size: 9.2px; line-height: 11.5px; }
  .stars { margin-top: 6px; font-size: 7px; letter-spacing: 2px; }
  .social-bottom { left: 185px; top: 1169px; }
</style>
</head>
<body class="wood">
  <header>
    <div class="abs brand"><span class="brand-mark"></span>Treval Buildworks</div>
    <div class="abs social social-top" aria-label="Social links"><span></span><span></span><span></span><span></span></div>
    <div class="abs phone">+1 (555) 014-2437</div>
    <nav class="abs main-nav">
      <span>KITCHENS</span><span>BATHS</span><span>BASEMENTS</span><span>FINISHED CARPENTRY</span><span>DECKS &amp; PORCHES</span>
    </nav>
  </header>

  <section class="services">
    <h2 class="abs section-title" style="top:88px">My<br>Services</h2>
    <div class="abs plank wood" style="top:147px"></div>
    <div class="abs side-copy" style="top:184px">
      <p>3D CAD modelling of new<br>spaces</p>
      <p>Custom<br>carpentry &amp; finishes,</p>
      <p>Kitchens,<br>baths,<br>basements,<br>decks,<br>porches,</p>
      <p class="lead">Whole house<br>renovation</p>
      <p>Skilled craftsmanship<br>(hardwood flooring,<br>floor and wall tile)</p>
      <p>And much more</p>
    </div>
    <div class="abs frame wood" style="top:185px;height:245px">
      <div class="frame-media media-cad" role="img" aria-label="Kitchen shown from CAD line drawing to 3D model to finished photo">
        <div style="background:#8d8d8d"></div>
        <div style="background:linear-gradient(90deg,#8a8a8a,#6f6f6f)"></div>
        <div style="background:linear-gradient(90deg,#7a4a35,#a6725a,#6a3e2c)"></div>
      </div>
    </div>
  </section>

  <section class="work">
    <h2 class="abs section-title" style="top:457px">Browse<br>My Work</h2>
    <div class="abs plank wood" style="top:516px"></div>
    <div class="abs side-copy" style="top:552px;width:80px;left:32px">Brose my work in before and after photos</div>
    <svg class="abs arrows" width="56" height="16" viewBox="0 0 56 16" aria-label="Previous and next">
      <path d="M8 2 L2 8 L8 14" fill="none" stroke="#2b1f15" stroke-width="2"/>
      <path d="M42 2 L48 8 L42 14" fill="none" stroke="#2b1f15" stroke-width="2"/>
    </svg>
    <div class="abs thumb" role="img" aria-label="Stone fireplace corner beside a dark hardwood floor"></div>
    <div class="abs social social-mid" aria-label="Share links"><span></span><span></span><span></span><span></span></div>
    <div class="abs frame wood" style="top:553px;height:247px">
      <div class="frame-media" role="img" aria-label="Polished granite countertop curving beside wood kitchen cabinets"
           style="background:linear-gradient(160deg,#c9a88a 0%,#8a5530 35%,#6a3a22 70%,#4a2a1a 100%)"></div>
    </div>
  </section>

  <section class="testimonials">
    <h2 class="abs section-title" style="top:826px">Client<br>Testimonials</h2>
    <div class="abs plank wood" style="top:885px"></div>
    <div class="abs side-copy" style="top:922px;width:104px">Read what our<br>satistied<br>clients have to say<br>about our services and<br>expertise</div>
    <div class="abs cards">
      <article class="card">
        <div class="card-photo" role="img" aria-label="Client portrait"></div>
        <p>Lorem ipsum dolor sit<br>amet, consectetur<br>adipiscing elit ...</p>
        <p class="card-name">JOHN DOE</p><p class="card-role">Entrepreneur</p><p class="stars">★★★★★</p>
      </article>
      <article class="card">
        <div class="card-photo" role="img" aria-label="Client portrait"></div>
        <p>Lorem ipsum dolor sit<br>amet, consectetur<br>adipiscing elit ...</p>
        <p class="card-name">JOHN DOE</p><p class="card-role">Entrepreneur</p><p class="stars">★★★★★</p>
      </article>
      <article class="card">
        <div class="card-photo" role="img" aria-label="Client portrait"></div>
        <p>Lorem ipsum dolor sit<br>amet, consectetur<br>adipiscing elit ...</p>
        <p class="card-name">JOHN DOE</p><p class="card-role">Entrepreneur</p><p class="stars">★★★★★</p>
      </article>
      <article class="card">
        <div class="card-photo" role="img" aria-label="Client portrait"></div>
        <p>Lorem ipsum dolor sit<br>amet, consectetur<br>adipiscing elit ...</p>
        <p class="card-name">JOHN DOE</p><p class="card-role">Entrepreneur</p><p class="stars">★★★★★</p>
      </article>
    </div>
  </section>

  <footer class="abs social social-bottom" aria-label="Social links"><span></span><span></span><span></span><span></span></footer>
</body>
</html>
```